Business Card for: Bramwell Financial Advisory Services Inc.

provide strategic financial advisory services to companies in the areas of corporate finance, mergers and acquisitions, executive coaching and strategic planning

Target Market(s)

Companies, banks, accountants, lawyers

Industry/Entity Type

High end business consulting in corporate finance, mergers and acquisitions, consulting

Contact Information for Business Card

Name of company, Name: xxxxxx xxxxxx , CEO, - phone number: 1-xxx-xxx-xxxx, - email address,

Requirements
Must have
• Must be professional and simple.
Nice to have
• simple, straight graphics, must give the impression that we are trustworthy, professional, competent
Should not have
• loud colors, loud design features

```html
<!DOCTYPE html>
<html lang="en">
<head>
<meta charset="utf-8">
<title>Bramwell Financial Advisory Services Inc. – Business Card</title>
<link rel="stylesheet" href="https://fonts.googleapis.com/css2?family=Open+Sans:wght@400;600;700&display=swap">
<style>
  :root {
    --board: #b8e4f7;
    --label: #3f6a9c;
    --card-front: #e9eddd;
    --navy: #25226b;
    --card-back: #201c50;
    --white: #ffffff;
  }
  * { box-sizing: border-box; margin: 0; padding: 0; }
  html, body {
    width: 1091px;
    height: 1200px;
    overflow: hidden;
    background: var(--board);
    font-family: "Open Sans", sans-serif;
  }
  .board {
    position: relative;
    width: 1091px;
    height: 1200px;
  }
  .side-label {
    position: absolute;
    font-size: 38px;
    font-weight: 600;
    color: var(--label);
    line-height: 1;
  }
  .side-label--front { left: 105px; top: 24px; }
  .side-label--back { left: 105px; top: 600px; }

  .card {
    position: absolute;
    left: 105px;
    width: 880px;
    height: 500px;
    overflow: hidden;
  }
  .card--front { top: 78px; background: var(--card-front); }
  .card--back { top: 656px; background: var(--card-back); }

  .name-band {
    position: absolute;
    left: 0;
    top: 148px;
    width: 487px;
    height: 95px;
    background: var(--navy);
    border-radius: 0 48px 48px 0;
    padding: 10px 0 0 56px;
    color: var(--white);
  }
  .name-band__name {
    font-size: 32px;
    font-weight: 700;
    line-height: 1.2;
  }
  .name-band__title {
    font-size: 24px;
    font-weight: 400;
    line-height: 1.2;
  }

  .contact-list {
    position: absolute;
    left: 60px;
    top: 282px;
    list-style: none;
    color: var(--navy);
    font-size: 25px;
  }
  .contact-list__item {
    display: flex;
    align-items: center;
    gap: 18px;
    height: 45px;
  }
  .contact-list__icon { width: 22px; height: 22px; flex: none; }

  .company-name {
    position: absolute;
    display: flex;
    align-items: center;
    gap: 12px;
  }
  .company-name--front { left: 555px; top: 228px; color: var(--navy); }
  .company-name--back { left: 292px; top: 216px; color: var(--white); }
  .company-name__dot {
    width: 40px;
    height: 40px;
    border-radius: 50%;
    background: currentColor;
    flex: none;
  }
  .company-name__text { display: flex; flex-direction: column; }
  .company-name__main {
    font-size: 33px;
    font-weight: 700;
    line-height: 1.05;
  }
  .company-name__sub {
    font-size: 15px;
    font-weight: 700;
    line-height: 1.2;
  }
</style>
</head>
<body>
<main class="board">
  <h2 class="side-label side-label--front">front</h2>
  <section class="card card--front" aria-label="Business card front">
    <div class="name-band">
      <p class="name-band__name">Your Name Here</p>
      <p class="name-band__title">CEO</p>
    </div>
    <ul class="contact-list">
      <li class="contact-list__item">
        <svg class="contact-list__icon" viewBox="0 0 24 24" aria-hidden="true">
          <path fill="currentColor" d="M6.6 10.8c1.4 2.8 3.8 5.1 6.6 6.6l2.2-2.2c.3-.3.7-.4 1-.2 1.1.4 2.3.6 3.6.6.6 0 1 .4 1 1V20c0 .6-.4 1-1 1C10.6 21 3 13.4 3 4c0-.6.4-1 1-1h3.5c.6 0 1 .4 1 1 0 1.3.2 2.5.6 3.6.1.3 0 .7-.2 1z"/>
        </svg>
        <span>1-XXX-XXX-XXXX</span>
      </li>
      <li class="contact-list__item">
        <svg class="contact-list__icon" viewBox="0 0 24 24" aria-hidden="true">
          <rect x="2" y="5" width="20" height="14" rx="1" fill="currentColor"/>
          <polyline points="2,6 12,13 22,6" fill="none" stroke="#e9eddd" stroke-width="1.8"/>
        </svg>
        <span>email@company.com</span>
      </li>
    </ul>
    <div class="company-name company-name--front">
      <span class="company-name__dot" aria-hidden="true"></span>
      <span class="company-name__text">
        <span class="company-name__main">Bramwell</span>
        <span class="company-name__sub">Financial Advisory Inc.</span>
      </span>
    </div>
  </section>

  <h2 class="side-label side-label--back">Back</h2>
  <section class="card card--back" aria-label="Business card back">
    <div class="company-name company-name--back">
      <span class="company-name__dot" aria-hidden="true"></span>
      <span class="company-name__text">
        <span class="company-name__main">Bramwell</span>
        <span class="company-name__sub">Financial Advisory Inc.</span>
      </span>
    </div>
  </section>
</main>
</body>
</html>
```